Residential Remodeling Contractor needs updated business card

I need a new design for my business card.
Name of the company is Ridgefell Construction. I need a card that commands presence, strength, integrity. I have been in business for 28 years. I am a Residential Remodeling Contractor that covers all aspects of a residential remodel and build.

```html
<!DOCTYPE html>
<html lang="en">
<head>
<meta charset="utf-8">
<title>Ridgefell Construction – Business Card</title>
<link href="https://fonts.googleapis.com/css2?family=Arimo:wght@400;700&display=swap" rel="stylesheet">
<style>
  :root {
    --backdrop: #1f1f21;
    --card-blue: #1a3f86;
    --card-blue-deep: #163672;
    --ink-white: #ffffff;
    --ink-soft: rgba(255,255,255,0.88);
    --rule: rgba(255,255,255,0.75);
  }
  * { margin: 0; padding: 0; box-sizing: border-box; }
  html, body {
    width: 1200px; height: 801px; overflow: hidden;
    background: var(--backdrop);
    font-family: "Arimo", Arial, sans-serif;
  }
  .canvas {
    position: relative; width: 1200px; height: 801px;
    display: flex; align-items: center; justify-content: center; gap: 40px;
  }
  .card {
    position: relative; width: 540px; height: 309px;
    border-radius: 22px;
    background: linear-gradient(135deg, var(--card-blue) 0%, var(--card-blue-deep) 100%);
    color: var(--ink-white);
    overflow: hidden;
    box-shadow: 0 18px 40px rgba(0,0,0,0.55);
  }
  /* Front: contact side */
  .brand {
    display: flex; align-items: center; gap: 10px;
    font-weight: 700; color: var(--ink-white); letter-spacing: 0.04em;
    text-transform: uppercase; line-height: 1.05;
  }
  .brand-mark { background: var(--ink-white); flex: none; }
  .card-front .brand { position: absolute; top: 46px; right: 40px; font-size: 22px; }
  .card-front .brand-mark { width: 14px; height: 14px; }
  .divider {
    position: absolute; left: 36px; right: 36px; top: 168px;
    height: 1px; background: var(--rule);
  }
  .person { position: absolute; left: 36px; top: 112px; }
  .person-name { font-size: 24px; font-weight: 700; letter-spacing: 0.02em; text-transform: uppercase; }
  .person-role { font-size: 13px; color: var(--ink-soft); margin-top: 4px; }
  .contacts { position: absolute; left: 36px; top: 186px; list-style: none; }
  .contacts li {
    display: flex; align-items: center; gap: 9px;
    font-size: 14px; line-height: 1; margin-bottom: 10px; color: var(--ink-soft);
  }
  .contacts svg { width: 12px; height: 12px; fill: var(--ink-white); flex: none; }
  .address {
    position: absolute; right: 36px; top: 186px; text-align: right;
    font-size: 13px; line-height: 1.5; color: var(--ink-soft);
  }
  /* Back: brand side */
  .card-back { display: flex; align-items: center; justify-content: center; }
  .card-back .brand { font-size: 38px; gap: 16px; }
  .card-back .brand-mark { width: 22px; height: 22px; }
</style>
</head>
<body>
<main class="canvas">
  <section class="card card-front" aria-label="Business card front">
    <div class="brand"><span class="brand-mark"></span><span>Ridgefell<br>Construction</span></div>
    <div class="person">
      <h1 class="person-name">Marco Delvane</h1>
      <p class="person-role">Owner &amp; Manager</p>
    </div>
    <div class="divider"></div>
    <ul class="contacts">
      <li>
        <svg viewBox="0 0 24 24" aria-hidden="true"><path d="M6.6 10.8a15.1 15.1 0 0 0 6.6 6.6l2.2-2.2a1 1 0 0 1 1-.25 11.4 11.4 0 0 0 3.6.57 1 1 0 0 1 1 1V20a1 1 0 0 1-1 1A17 17 0 0 1 3 4a1 1 0 0 1 1-1h3.5a1 1 0 0 1 1 1c0 1.25.2 2.45.57 3.6a1 1 0 0 1-.25 1z"/></svg>
        555 214 7390
      </li>
      <li>
        <svg viewBox="0 0 24 24" aria-hidden="true"><path d="M2 5h20v14H2zm2 2v.4l8 5 8-5V7zm0 2.8V17h16V9.8l-8 5z"/></svg>
        info@ridgefellconstruction.com
      </li>
      <li>
        <svg viewBox="0 0 24 24" aria-hidden="true"><path d="M12 2a10 10 0 1 0 0 20 10 10 0 0 0 0-20zm6.9 9h-3a15 15 0 0 0-1.3-6 8 8 0 0 1 4.3 6zM12 4.1c.9 1.3 1.7 3.7 1.9 6.9h-3.8c.2-3.2 1-5.6 1.9-6.9zM4.1 13h3a15 15 0 0 0 1.3 6 8 8 0 0 1-4.3-6zm3-2h-3a8 8 0 0 1 4.3-6 15 15 0 0 0-1.3 6zM12 19.9c-.9-1.3-1.7-3.7-1.9-6.9h3.8c-.2 3.2-1 5.6-1.9 6.9zm2.6-.9a15 15 0 0 0 1.3-6h3a8 8 0 0 1-4.3 6z"/></svg>
        www.ridgefellconstruction.com
      </li>
    </ul>
    <p class="address">P.O. Box Street Name<br>Country Name AB, A5B 521</p>
  </section>

  <section class="card card-back" aria-label="Business card back">
    <div class="brand"><span class="brand-mark"></span><span>Ridgefell<br>Construction</span></div>
  </section>
</main>
</body>
</html>
```